Velvet Pressings Techno Label Business Card

I'm looking for a very clean business card for my Velvet Pressings music label. The label focusses on techno music. The card should include:

• my name : Tomas Brandt as "Founder & CEO"
• email address: tomas@velvet-pressings.example
• web: www.velvet-pressings.example
• facebook logo + /velvetpress
• twitter logo + /velvetpress
• soundcloud logo + /velvetpressings

Feel free to include your ideas! I'm looking forward to discuss about it.

Tomas

Industry/Entity Type

Business

Contact Information for Business Card

I don't like glossy cards. Prefer matt.

Requirements
Nice to have
• Maybe on one side the complete logo, other side just the icon.
Should not have
• Flashy stuff. Must be clean and business like style.

```html
<!DOCTYPE html>
<html lang="en">
<head>
<meta charset="utf-8">
<title>Velvet Pressings – Business Card</title>
<link rel="stylesheet" href="https://fonts.googleapis.com/css2?family=Arimo:wght@700&family=Montserrat:wght@300;400;500&display=swap">
<style>
  :root {
    --orange: #f47216;
    --orange-deep: #e8620c;
    --paper: #f7f7f7;
    --stage: #ebebeb;
    --ink: #3c3c3c;
    --ink-soft: #6d6d6d;
    --rule: #dcdcdc;
    --white: #ffffff;
  }
  * { margin: 0; padding: 0; box-sizing: border-box; }
  html, body {
    width: 1200px;
    height: 726px;
    overflow: hidden;
    background: var(--stage);
  }
  .stage {
    position: relative;
    width: 1200px;
    height: 726px;
  }
  .card {
    position: absolute;
    top: 214px;
    width: 520px;
    height: 298px;
    box-shadow: 0 6px 18px rgba(0,0,0,0.12);
  }

  /* Front side */
  .card--front {
    left: 50px;
    background: var(--orange);
    display: flex;
    align-items: center;
    padding-left: 64px;
  }
  .brand {
    display: flex;
    align-items: center;
    gap: 16px;
  }
  .brand__dot {
    width: 46px;
    height: 46px;
    border-radius: 50%;
    background: var(--white);
    flex: none;
  }
  .brand__name {
    font-family: "Arimo", Arial, sans-serif;
    font-weight: 700;
    font-size: 36px;
    letter-spacing: -0.5px;
    color: var(--white);
  }

  /* Back side */
  .card--back {
    left: 630px;
    background: var(--paper);
    border-top: 8px solid var(--orange);
    border-bottom: 8px solid var(--orange);
    display: flex;
  }
  .back__mark {
    width: 45%;
    border-right: 1px solid var(--rule);
    display: flex;
    align-items: center;
    justify-content: center;
    gap: 10px;
  }
  .back__mark-square {
    width: 14px;
    height: 14px;
    background: var(--orange);
    flex: none;
  }
  .back__mark-name {
    font-family: "Montserrat", Arial, sans-serif;
    font-weight: 500;
    font-size: 20px;
    color: var(--orange);
  }
  .back__details {
    flex: 1;
    display: flex;
    flex-direction: column;
    justify-content: space-between;
    align-items: flex-end;
    padding: 28px 28px 24px 20px;
    text-align: right;
  }
  .person__name {
    font-family: "Montserrat", Arial, sans-serif;
    font-weight: 400;
    font-size: 19px;
    letter-spacing: 0.5px;
    color: var(--orange);
  }
  .person__title {
    font-family: "Montserrat", Arial, sans-serif;
    font-weight: 400;
    font-size: 11px;
    color: var(--ink-soft);
    margin-top: 3px;
  }
  .contact {
    list-style: none;
    font-family: "Montserrat", Arial, sans-serif;
    font-weight: 500;
    font-size: 11px;
    line-height: 14px;
    color: var(--ink);
  }
  .contact__item {
    display: flex;
    align-items: center;
    justify-content: flex-end;
    gap: 8px;
    margin-top: 5px;
    white-space: nowrap;
  }
  .contact__item--social {
    color: var(--ink-soft);
  }
  .contact__icon {
    width: 12px;
    height: 12px;
    flex: none;
  }
  .contact__dot {
    width: 12px;
    height: 12px;
    border-radius: 50%;
    background: var(--orange);
    flex: none;
  }
</style>
</head>
<body>
<main class="stage">

  <section class="card card--front" aria-label="Card front">
    <div class="brand">
      <span class="brand__dot"></span>
      <span class="brand__name">Velvet Pressings</span>
    </div>
  </section>

  <section class="card card--back" aria-label="Card back">
    <div class="back__mark">
      <span class="back__mark-square"></span>
      <span class="back__mark-name">Velvet Pressings</span>
    </div>
    <div class="back__details">
      <div class="person">
        <p class="person__name">Tomas Brandt</p>
        <p class="person__title">Founder &amp; CEO</p>
      </div>
      <ul class="contact">
        <li class="contact__item">
          <span>tomas@velvet-pressings.example</span>
          <svg class="contact__icon" viewBox="0 0 12 12" aria-hidden="true">
            <rect x="0.5" y="2.5" width="11" height="7.5" fill="var(--orange)"/>
            <polyline points="0.8,2.8 6,7 11.2,2.8" fill="none" stroke="var(--white)" stroke-width="1"/>
          </svg>
        </li>
        <li class="contact__item">
          <span>www.velvet-pressings.example</span>
          <svg class="contact__icon" viewBox="0 0 12 12" aria-hidden="true">
            <circle cx="6" cy="6" r="5.5" fill="var(--orange)"/>
            <ellipse cx="6" cy="6" rx="2.3" ry="5.3" fill="none" stroke="var(--white)" stroke-width="0.8"/>
            <line x1="0.6" y1="6" x2="11.4" y2="6" stroke="var(--white)" stroke-width="0.8"/>
          </svg>
        </li>
        <li class="contact__item contact__item--social">
          <span>/velvetpress</span>
          <span class="contact__dot" aria-hidden="true"></span>
        </li>
        <li class="contact__item contact__item--social">
          <span>/velvetpress</span>
          <span class="contact__dot" aria-hidden="true"></span>
        </li>
        <li class="contact__item contact__item--social">
          <span>/velvetpressings</span>
          <span class="contact__dot" aria-hidden="true"></span>
        </li>
      </ul>
    </div>
  </section>

</main>
</body>
</html>
```